Business card design for holistic health care clinic

We need a double-sided business card design for our holistic health care clinic that integrates our logo design and also its color scheme. My business is called Valmira. It is an integrative medicine clinic. You have already done the logo for me. Please ensure an elegant and upscale design that is not cluttered, but still has all the necessary information (please see below for details).

Target Market(s)

Wellness, fitness, rehabilitation for educated, well-traveled open-minded clients who are focused on natural, organic, balanced and preventive healthcare and lifestyle.

Industry/Entity Type

Medical

Contact Information for Business Card

Modern, clean.

Number of Pages Required

1 page

Font styles to use
Serif
Sans Serif

Colors

Designer to choose colors to be used in the design.

Requirements
Must have
• Logo on one side, all other information on the other side.
• Other information should include:
• Tobias Wrenfeld - DOE, CPT, LMT
• 4100 East Marrow Drive
• Austin, TX 78119
• 512 555 0148
• 818 555 0192
• info@ValmiraHealth.example
• t.wrenfeld@ValmiraHealth.example
Nice to have
• Darker background on front - but not totally black - shaded/dark gray.

```html
<!DOCTYPE html>
<html lang="en">
<head>
<meta charset="utf-8">
<title>Valmira Business Card</title>
<link rel="stylesheet" href="https://fonts.googleapis.com/css2?family=Montserrat:wght@300;400;600;700&display=swap">
<style>
  :root {
    --backdrop: #d9cdbd;
    --card-frost: #eef1f1;
    --brand-teal: #1f8fb0;
    --band-teal: #3ba5bf;
    --band-deep: #2f95b0;
    --ink-cream: #eee2c9;
    --ink-cream-soft: #e3d6bd;
  }
  * { margin: 0; padding: 0; box-sizing: border-box; }
  html, body {
    width: 1200px;
    height: 1047px;
    overflow: hidden;
  }
  body {
    background: var(--backdrop);
    font-family: "Montserrat", sans-serif;
    position: relative;
  }
  .business-card {
    position: absolute;
    left: 100px;
    top: 248px;
    width: 1000px;
    height: 550px;
    border-radius: 22px;
    background: var(--card-frost);
    overflow: hidden;
    box-shadow: 0 18px 40px rgba(60, 45, 30, 0.22);
  }
  .brand-block {
    position: absolute;
    left: 52px;
    top: 92px;
    color: var(--brand-teal);
  }
  .brand-name {
    display: flex;
    align-items: center;
    gap: 18px;
    font-weight: 700;
    font-size: 92px;
    line-height: 1;
    letter-spacing: 1px;
  }
  .brand-dot {
    width: 30px;
    height: 30px;
    border-radius: 50%;
    background: var(--brand-teal);
  }
  .brand-tagline {
    margin-top: 8px;
    margin-left: 4px;
    font-weight: 600;
    font-size: 25px;
    letter-spacing: 0.3px;
  }
  .info-band {
    position: absolute;
    left: 0;
    top: 277px;
    width: 100%;
    height: 273px;
    background: linear-gradient(90deg, var(--band-teal) 0%, var(--band-deep) 45%, var(--band-teal) 100%);
    color: var(--ink-cream);
  }
  .person-name {
    position: absolute;
    left: 48px;
    top: 30px;
    font-weight: 600;
    font-size: 40px;
    letter-spacing: 1px;
    text-transform: uppercase;
  }
  .person-credentials {
    position: absolute;
    left: 50px;
    top: 84px;
    font-weight: 300;
    font-size: 20px;
    letter-spacing: 0.5px;
    color: var(--ink-cream-soft);
  }
  .contact-list {
    position: absolute;
    left: 48px;
    top: 126px;
    list-style: none;
  }
  .contact-item {
    display: flex;
    align-items: center;
    gap: 14px;
    height: 30px;
    font-weight: 300;
    font-size: 21px;
    letter-spacing: 0.3px;
  }
  .contact-icon {
    width: 16px;
    height: 16px;
    flex: none;
  }
  .address {
    position: absolute;
    right: 263px;
    top: 180px;
    text-align: right;
    font-style: normal;
    font-weight: 300;
    font-size: 21px;
    line-height: 30px;
    letter-spacing: 0.3px;
  }
</style>
</head>
<body>
  <section class="business-card">
    <header class="brand-block">
      <div class="brand-name"><span class="brand-dot"></span>VALMIRA</div>
      <div class="brand-tagline">Integrative Holistic Medicine</div>
    </header>

    <div class="info-band">
      <h1 class="person-name">Tobias Wrenfeld</h1>
      <p class="person-credentials">DOE, CPT, LMT</p>

      <ul class="contact-list">
        <li class="contact-item">
          <svg class="contact-icon" viewBox="0 0 16 16" fill="none" stroke="currentColor" stroke-width="1.6" stroke-linejoin="round">
            <path d="M3 1.5h3l1.2 3.3-1.8 1.2a8 8 0 0 0 4.6 4.6l1.2-1.8 3.3 1.2v3a1.5 1.5 0 0 1-1.6 1.5A12.5 12.5 0 0 1 1.5 3.1 1.5 1.5 0 0 1 3 1.5z"/>
          </svg>
          <span>512 555 0148</span>
        </li>
        <li class="contact-item">
          <svg class="contact-icon" viewBox="0 0 16 16" fill="none" stroke="currentColor" stroke-width="1.6">
            <rect x="4" y="1" width="8" height="14" rx="1.5"/>
            <line x1="7" y1="12.5" x2="9" y2="12.5"/>
          </svg>
          <span>818 555 0192</span>
        </li>
        <li class="contact-item">
          <svg class="contact-icon" viewBox="0 0 16 16" fill="none" stroke="currentColor" stroke-width="1.6" stroke-linejoin="round">
            <rect x="1.5" y="3.5" width="13" height="9" rx="1"/>
            <path d="M1.5 4l6.5 5 6.5-5"/>
          </svg>
          <span>info@ValmiraHealth.example</span>
        </li>
        <li class="contact-item">
          <svg class="contact-icon" viewBox="0 0 16 16" fill="none" stroke="currentColor" stroke-width="1.4">
            <circle cx="8" cy="8" r="6.5"/>
            <ellipse cx="8" cy="8" rx="2.8" ry="6.5"/>
            <line x1="1.5" y1="8" x2="14.5" y2="8"/>
          </svg>
          <span>t.wrenfeld@ValmiraHealth.example</span>
        </li>
      </ul>

      <address class="address">
        4100 East Marrow Drive<br>
        Austin, TX 78119
      </address>
    </div>
  </section>
</body>
</html>
```